BOLD & MINIMALIST DESIGN NEEDED

We want a very bold but minimalistic business card design that is impactful and utilizes both sides of the business card. Our current logo is included for your use.

We want bold fonts and good use of negative space. We don't want the logo to overpower the design.

Target Market(s)

Professionals who are building new commercial buildings.

Industry/Entity Type

Construction

Contact Information for Business Card

Name, Title, email, office phone, cell phone, website

Font styles to use
Serif
Sans Serif

Requirements
Must have
• Bold design!

```html
<!DOCTYPE html>
<html lang="en">
<head>
<meta charset="UTF-8">
<title>Ridgeline Design + Build — Business Card</title>
<link rel="stylesheet" href="https://fonts.googleapis.com/css2?family=Montserrat:wght@400;500;700;800&display=swap">
<style>
  :root {
    --backdrop: #141414;
    --card: #2a2a2a;
    --card-edge: #232323;
    --accent: #8cc63f;
    --ink: #f2f2f2;
    --ink-soft: #d6d6d6;
    --emboss: #3a3a3a;
  }
  * { margin: 0; padding: 0; box-sizing: border-box; }
  html, body {
    width: 1200px; height: 900px; overflow: hidden;
    background: var(--backdrop);
    font-family: "Montserrat", sans-serif;
  }
  .stage {
    width: 1200px; height: 900px;
    display: flex; flex-direction: column;
    align-items: center; justify-content: center; gap: 46px;
  }
  .card {
    position: relative;
    width: 680px; height: 388px;
    background: linear-gradient(160deg, var(--card) 0%, var(--card-edge) 100%);
    border-bottom: 6px solid var(--accent);
    box-shadow: 0 18px 40px rgba(0,0,0,.55);
    overflow: hidden;
  }

  /* Back side */
  .card-back { display: flex; align-items: center; justify-content: center; }
  .back-wordmark {
    font-weight: 800; font-size: 58px; letter-spacing: 2px;
    color: var(--emboss); text-transform: uppercase;
  }

  /* Front side */
  .card-front { display: flex; align-items: center; padding: 0 40px 0 44px; }
  .brand {
    width: 250px; display: flex; align-items: center; gap: 12px;
  }
  .brand-mark { width: 22px; height: 22px; background: var(--accent); flex: none; }
  .brand-name {
    font-weight: 800; font-size: 30px; line-height: 1.05;
    color: var(--ink); text-transform: uppercase;
  }
  .divider { width: 3px; height: 216px; background: var(--accent); margin: 0 36px 0 30px; flex: none; }
  .details { color: var(--ink-soft); }
  .person-name {
    font-weight: 800; font-size: 30px; letter-spacing: 2px;
    color: var(--accent); text-transform: uppercase; line-height: 1;
  }
  .person-title {
    font-weight: 500; font-size: 15px; letter-spacing: 1px;
    color: var(--ink); text-transform: uppercase; margin-top: 4px;
  }
  .address { font-size: 15px; line-height: 1.35; margin-top: 24px; color: var(--ink); }
  .contacts { list-style: none; margin-top: 22px; }
  .contacts li {
    display: flex; align-items: center; gap: 10px;
    font-size: 15px; line-height: 1.6; color: var(--ink);
  }
  .contacts svg { width: 16px; height: 16px; flex: none; }
  .web-highlight { color: var(--accent); }
</style>
</head>
<body>
<main class="stage">

  <section class="card card-back" aria-label="Card back">
    <span class="back-wordmark">Ridgeline</span>
  </section>

  <section class="card card-front" aria-label="Card front">
    <div class="brand">
      <span class="brand-mark"></span>
      <span class="brand-name">Ridgeline<br>Design + Build</span>
    </div>
    <div class="divider"></div>
    <div class="details">
      <h1 class="person-name">Mark Ellison</h1>
      <p class="person-title">Owner</p>
      <p class="address">4807 Timber Lane,<br>Suite #310</p>
      <ul class="contacts">
        <li>
          <svg viewBox="0 0 16 16" aria-hidden="true"><rect x="4" y="1" width="8" height="14" rx="1.5" fill="none" stroke="#8cc63f" stroke-width="1.6"/><circle cx="8" cy="12.5" r="0.9" fill="#8cc63f"/></svg>
          (555) 214-3870
        </li>
        <li>
          <svg viewBox="0 0 16 16" aria-hidden="true"><path d="M3 2l3 0 1 3-2 1.5c1 2 2.5 3.5 4.5 4.5L11 9l3 1v3c0 .6-.5 1-1 1C7 14 2 9 2 3c0-.5.4-1 1-1z" fill="#8cc63f"/></svg>
          (555) 214-3870
        </li>
        <li>
          <svg viewBox="0 0 16 16" aria-hidden="true"><rect x="1.5" y="3.5" width="13" height="9" fill="none" stroke="#8cc63f" stroke-width="1.4"/><path d="M1.5 3.5L8 9l6.5-5.5" fill="none" stroke="#8cc63f" stroke-width="1.4"/></svg>
          ridgelinebuild@mail.com
        </li>
        <li>
          <svg viewBox="0 0 16 16" aria-hidden="true"><circle cx="8" cy="8" r="6.3" fill="none" stroke="#8cc63f" stroke-width="1.3"/><ellipse cx="8" cy="8" rx="2.8" ry="6.3" fill="none" stroke="#8cc63f" stroke-width="1.1"/><path d="M1.7 8h12.6M2.8 4.8h10.4M2.8 11.2h10.4" stroke="#8cc63f" stroke-width="1"/></svg>
          <span>www.<span class="web-highlight">ridgelinebuild</span>.com</span>
        </li>
      </ul>
    </div>
  </section>

</main>
</body>
</html>
```